Current website re-design to a updated look and feel.

We currently have a website www.brightlanefreight.com that we want to give an updated look and feel to. We are a logistics company that competes with Pellwick, Dm Harrowgate, Quill but on a smaller scale. We want something fresh and updated. We have two locations one in downtown Marrowfield and one in Kestrel Park. We are a fun group that also gets the job done. We know we need pictures of both locations and possibly a video, but we need fresh design ideas. The 'who we are' page is really the only page that we currently want to keep. The 'what we do' page needs to be completely re-done from a look and feel for sure.

Target Market(s)

Anyone who uses Truck transportation to move their product. Mainly US manufacturers.

Industry/Entity Type

Logistics

Number of Pages Required

5+ page

Font styles to use
Sans Serif

Colors
5c91c4
0355a3
d0dfed

Requirements
Must have
• The new design must entice people to want to do business with us. The design must have locations for pictures and at least one video which we know we will have to provide. Design must be easy to navigate.

```html
<!DOCTYPE html>
<html lang="en">
<head>
<meta charset="utf-8">
<title>Brightlane Transportation</title>
<link href="https://fonts.googleapis.com/css2?family=Cinzel:wght@400;700&family=Roboto+Condensed:ital,wght@0,400;0,700;1,400&family=Roboto:ital,wght@0,400;0,500;0,700;1,400&display=swap" rel="stylesheet">
<style>
:root{
  --blue:#0355a3;
  --sky:#5c91c4;
  --pale:#d0dfed;
  --mid:#1a7ec3;
  --deep:#024a8f;
  --ink:#3f4650;
  --muted:#7a8290;
  --light:#f4f6f9;
  --white:#ffffff;
}
*{box-sizing:border-box;margin:0;padding:0}
html,body{width:1200px;height:4327px;overflow:hidden}
body{font-family:"Roboto",Arial,sans-serif;color:var(--ink);background:var(--white);position:relative}
section,header,footer{position:absolute;left:0;width:1200px}
.title{font-family:"Cinzel",Georgia,serif;font-weight:400;text-align:center;color:var(--blue);font-size:42px;letter-spacing:1px}
.subtitle{font-style:italic;text-align:center;color:var(--muted);font-size:16px}
ul{list-style:none}

/* header */
.site-header{top:0;height:110px;background:var(--white);box-shadow:0 2px 6px rgba(0,0,0,.08);z-index:2}
.brand{position:absolute;left:78px;top:22px;display:flex;align-items:center;gap:12px}
.brand-name{font-family:"Roboto",sans-serif;font-weight:700;font-size:40px;color:var(--blue);letter-spacing:-1px}
.brand-sub{font-size:11px;line-height:13px;color:var(--blue);font-weight:500}
.login{position:absolute;right:78px;top:14px;font-size:14px;color:var(--blue);display:flex;gap:6px;align-items:center}
.nav{position:absolute;right:78px;top:56px;display:flex;gap:28px;font-size:16px;font-weight:500;color:var(--blue)}
.nav li{position:relative;height:54px}
.nav .active::after{content:"";position:absolute;left:-6px;right:-6px;bottom:0;height:4px;background:var(--blue)}

/* hero */
.hero{top:110px;height:568px;background:linear-gradient(180deg,#6fa6d6 0%,#a9cbe6 35%,#4d85b6 55%,#7a5a4a 75%,#2e5a82 100%)}
.hero-arrow{position:absolute;top:244px;width:40px;height:40px;background:var(--blue);display:flex;align-items:center;justify-content:center}
.pin{position:absolute;display:flex;flex-direction:column;align-items:center;color:var(--white);font-size:14px;gap:6px}
.hero-title{position:absolute;left:520px;top:258px;font-family:"Roboto Condensed",sans-serif;font-weight:400;font-size:84px;color:var(--white)}
.hero-tag{position:absolute;left:524px;top:360px;font-style:italic;font-size:24px;color:var(--white)}
.btn-quote{position:absolute;left:520px;top:410px;width:226px;height:60px;border-radius:30px;background:var(--blue);color:var(--white);font-family:"Cinzel",serif;font-weight:700;font-size:18px;display:flex;align-items:center;justify-content:center}

/* welcome */
.welcome{top:678px;height:366px;background:var(--mid);color:var(--white);text-align:center}
.welcome .title{color:var(--white);padding-top:62px}
.welcome .lead{font-size:15px;margin-top:16px}
.welcome .body{width:780px;margin:16px auto 0;font-size:15px;line-height:28px;color:#e4eef8}
.btn-dark{display:inline-flex;align-items:center;justify-content:center;width:184px;height:58px;border-radius:29px;background:var(--blue);color:var(--white);font-family:"Cinzel",serif;font-weight:700;font-size:18px;margin-top:20px}

/* services */
.services{top:1044px;height:592px;background:var(--white)}
.services .title{padding-top:56px}
.services .subtitle{margin-top:8px}
.cards{position:absolute;top:162px;left:78px;display:flex;gap:18px}
.card{width:248px;height:366px;background:var(--white);box-shadow:0 2px 8px rgba(0,0,0,.12);text-align:center;position:relative}
.card .photo{height:184px}
.card .icon{position:absolute;left:94px;top:150px;width:60px;height:60px;border-radius:50%;background:var(--blue);display:flex;align-items:center;justify-content:center}
.card h3{font-family:"Cinzel",serif;font-weight:700;font-size:18px;color:var(--ink);margin-top:48px;line-height:22px}
.card p{font-size:14px;line-height:21px;color:var(--muted);margin:8px 22px 0}
.card .chev{position:absolute;left:114px;bottom:18px}
.card.is-featured{background:var(--blue)}
.card.is-featured h3,.card.is-featured p{color:var(--white)}
.card.is-featured .icon{background:var(--blue);border:3px solid var(--white)}

/* updates */
.updates{top:1636px;height:418px}
.updates .photo{position:absolute;left:0;top:0;width:600px;height:418px;background:linear-gradient(180deg,#b8d0e4 0%,#8eb0cc 40%,#5c7f97 58%,#3f6e94 100%)}
.updates .panel{position:absolute;left:600px;top:0;width:600px;height:418px;background:var(--blue);color:var(--white);text-align:center}
.updates .title{color:var(--white);padding-top:40px;font-size:40px}
.updates .panel p{font-size:15px;line-height:24px;width:470px;margin:14px auto 0}
.form{position:absolute;left:55px;top:172px;width:470px;display:grid;grid-template-columns:1fr 1fr;gap:8px 12px}
.field{height:54px;background:var(--white);border-radius:4px;color:#999;font-size:14px;text-align:left;padding:18px 12px}
.btn-outline{grid-column:1/3;margin-top:6px;height:62px;border:2px solid var(--white);border-radius:31px;display:flex;align-items:center;justify-content:center;font-family:"Cinzel",serif;font-weight:700;font-size:18px}

/* about */
.about{top:2054px;height:615px;background:var(--light)}
.about .title{padding-top:72px}
.about .subtitle{margin-top:10px}
.tabs{position:absolute;left:78px;top:184px;display:flex;gap:4px}
.tab{height:50px;background:#e3e6ea;color:var(--ink);font-family:"Cinzel",serif;font-size:18px;display:flex;align-items:center;justify-content:center}
.tab.is-active{background:var(--white);border-top:4px solid var(--blue);color:var(--blue);font-weight:700}
.tab-panel{position:absolute;left:78px;top:234px;width:514px;height:352px;background:var(--white)}
.founder-photo{position:absolute;left:10px;top:8px;width:156px;height:340px;background:linear-gradient(180deg,#eef1f4 0%,#c9b9a8 35%,#59605e 100%)}
.founder-text{position:absolute;left:176px;top:28px;width:316px}
.founder-text h4{font-family:"Cinzel",serif;color:var(--blue);font-size:20px}
.founder-text p{font-size:14px;line-height:24px;color:var(--muted);margin-top:10px}
.founder-text .sign{font-size:18px;color:var(--blue);margin-top:14px}
.about .photo{position:absolute;left:617px;top:182px;width:505px;height:404px;background:linear-gradient(180deg,#9fb7cc 0%,#6e8aa6 35%,#8a5a4c 65%,#3d4f66 100%)}
.live-chat{position:absolute;right:0;top:226px;width:44px;height:172px;background:var(--blue);border-radius:6px 0 0 6px;color:var(--white);font-weight:700;font-size:13px;display:flex;align-items:center;justify-content:center}
.live-chat span{transform:rotate(-90deg);white-space:nowrap}

/* testimonials */
.reviews{top:2669px;height:438px;background:linear-gradient(180deg,#2a6fb3 0%,#2462a6 60%,#1c5496 100%);color:var(--white);text-align:center}
.reviews .title{color:var(--white);padding-top:52px}
.reviews .subtitle{color:#dce8f4;margin-top:6px}
.avatar{width:110px;height:110px;border-radius:50%;border:4px solid var(--white);background:linear-gradient(180deg,#c7a98c,#6b5444);margin:24px auto 0}
.reviews blockquote{font-style:italic;font-size:17px;line-height:27px;width:900px;margin:22px auto 0}
.reviews cite{display:block;font-style:normal;margin-top:12px;font-size:17px}
.reviews cite b{font-family:"Cinzel",serif}
.rev-arrow{position:absolute;top:196px}

/* contact */
.contact{top:3107px;height:606px;background:var(--white)}
.contact .title{padding-top:62px}
.contact .subtitle{margin-top:4px}
.map{position:absolute;top:168px;width:330px;height:375px;background:linear-gradient(135deg,#eef0ea 0%,#e2e6dc 50%,#d9e1ea 100%);border:1px solid #d6d9dd}
.info{position:absolute;left:793px;top:190px;width:330px}
.info .brand-name{font-size:38px}
.info ul{margin-top:22px}
.info li{display:flex;gap:12px;font-size:14px;line-height:20px;margin-bottom:14px;align-items:flex-start}
.info li b{color:var(--blue)}
.socials{display:flex;gap:12px;margin-top:10px}
.socials i{width:46px;height:46px;border-radius:50%;display:block}

/* partners */
.partners{top:3713px;height:176px;background:var(--pale)}
.round-arrow{position:absolute;top:64px;width:46px;height:46px;border-radius:50%;border:2px solid var(--blue);display:flex;align-items:center;justify-content:center}
.badge{position:absolute;background:var(--white);border:2px solid #b7c9dc}

/* footer */
.site-footer{top:3889px;height:375px;background:var(--blue);color:var(--white)}
.col{position:absolute;top:42px}
.col h5{font-family:"Cinzel",serif;font-size:18px;letter-spacing:1px}
.col li{font-size:13px;line-height:21px;display:flex;gap:8px;align-items:center}
.col li::before{content:"";width:4px;height:4px;border-radius:50%;background:var(--white)}
.col p{font-size:14px;line-height:24px}
.subscribe-input{height:46px;background:var(--white);color:#888;font-size:13px;padding:15px 12px;margin-top:16px;width:246px}
.subscribe-btn{margin-top:12px;width:168px;height:54px;border:2px solid var(--white);border-radius:27px;display:flex;align-items:center;justify-content:center;font-family:"Cinzel",serif;font-weight:700;font-size:17px}
.bottom-bar{position:absolute;left:0;width:1200px;top:4264px;height:63px;background:#1565b0;color:var(--white);font-size:13px;display:flex;align-items:center;justify-content:center}
</style>
</head>
<body>

<header class="site-header">
  <div class="brand">
    <span class="brand-name">Brightlane</span>
    <span class="brand-sub">Transportation,<br>Distribution &amp;<br>Warehousing Inc.</span>
  </div>
  <div class="login">
    <svg width="14" height="14" viewBox="0 0 14 14"><circle cx="7" cy="4" r="3" fill="#0355a3"/><path d="M1 14c0-4 3-6 6-6s6 2 6 6z" fill="#0355a3"/></svg>
    Login
  </div>
  <ul class="nav">
    <li class="active">HOME</li><li>WHAT WE DO</li><li>HOW WE DO IT</li><li>WHO WE ARE</li><li>TRACKING</li><li>CHAT</li><li>CONTACT</li>
  </ul>
</header>

<section class="hero" role="img" aria-label="Container ship at port with stacked cargo containers under a blue sky">
  <div class="hero-arrow" style="left:0"><svg width="14" height="18" viewBox="0 0 14 18"><path d="M11 2 3 9l8 7" stroke="#fff" stroke-width="3" fill="none"/></svg></div>
  <div class="hero-arrow" style="right:0"><svg width="14" height="18" viewBox="0 0 14 18"><path d="m3 2 8 7-8 7" stroke="#fff" stroke-width="3" fill="none"/></svg></div>
  <div class="pin" style="left:52px;top:110px">
    <svg width="26" height="34" viewBox="0 0 26 34"><path d="M13 1C6 1 1 6 1 13c0 9 12 20 12 20s12-11 12-20C25 6 20 1 13 1z" fill="none" stroke="#0355a3" stroke-width="3"/><circle cx="13" cy="13" r="4" fill="#0355a3"/></svg>
    downtown Marrowfield
  </div>
  <div class="pin" style="left:372px;top:240px">
    <svg width="26" height="34" viewBox="0 0 26 34"><path d="M13 1C6 1 1 6 1 13c0 9 12 20 12 20s12-11 12-20C25 6 20 1 13 1z" fill="none" stroke="#0355a3" stroke-width="3"/><circle cx="13" cy="13" r="4" fill="#0355a3"/></svg>
    Kestrel Park
  </div>
  <h1 class="hero-title">Relax, we got this!</h1>
  <p class="hero-tag">Let us take the worry out of your logistics.</p>
  <div class="btn-quote">REQUEST QUOTE</div>
</section>

<section class="welcome">
  <h2 class="title">WELCOME TO BRIGHTLANE</h2>
  <p class="lead">Let us take the worry out of your logistics. Relax, we got this!</p>
  <p class="body">Brightlane Transportation welcomes you to our growing family of clients! We have over 26 years of experience in helping people solve their logistics needs from coast-to-coast. We also provide friendly, exceptional service that makes it easy to do business with us. Give us a call today and experience the difference for yourself!</p>
  <span class="btn-dark">KNOW MORE</span>
</section>

<section class="services">
  <h2 class="title">WHAT WE DO</h2>
  <p class="subtitle">We Provide Our Best Services</p>
  <div class="cards">
    <article class="card is-featured">
      <div class="photo" role="img" aria-label="Highway at dusk with freight traffic" style="background:linear-gradient(180deg,#e7a46a,#5c6f8a)"></div>
      <div class="icon"><svg width="28" height="28" viewBox="0 0 28 28"><rect x="5" y="8" width="18" height="16" fill="#fff"/><path d="M9 12l10 8M19 12 9 20" stroke="#0355a3" stroke-width="2"/><path d="M14 2v6" stroke="#fff" stroke-width="2"/></svg></div>
      <h3>FREIGHT MANAGEMENT</h3>
      <p>We strive for a perfect delivery and promise to be there for.</p>
      <svg class="chev" width="20" height="16" viewBox="0 0 20 16"><path d="M3 2l7 6 7-6M3 8l7 6 7-6" stroke="#fff" stroke-width="2" fill="none"/></svg>
    </article>
    <article class="card">
      <div class="photo" role="img" aria-label="Aerial view of container port cranes" style="background:linear-gradient(180deg,#9ab0c4,#596b7e)"></div>
      <div class="icon"><svg width="32" height="24" viewBox="0 0 32 24"><rect x="2" y="4" width="18" height="12" fill="#fff"/><path d="M20 8h6l4 5v3H20z" fill="#fff"/><circle cx="8" cy="19" r="3" fill="#fff"/><circle cx="24" cy="19" r="3" fill="#fff"/></svg></div>
      <h3>TRANSPORTATION</h3>
      <p>With a combined 500+ years of industry experience between.</p>
      <svg class="chev" width="20" height="16" viewBox="0 0 20 16"><path d="M3 2l7 6 7-6M3 8l7 6 7-6" stroke="#0355a3" stroke-width="2" fill="none"/></svg>
    </article>
    <article class="card">
      <div class="photo" role="img" aria-label="Bright warehouse interior with shelving" style="background:linear-gradient(180deg,#eef1f4,#b9c3cc)"></div>
      <div class="icon"><svg width="28" height="28" viewBox="0 0 28 28"><rect x="4" y="6" width="12" height="10" fill="#fff"/><path d="M18 4v18h7" stroke="#fff" stroke-width="2.5" fill="none"/><circle cx="8" cy="22" r="3" fill="#fff"/></svg></div>
      <h3>WAREHOUSE &amp;<br>DISTRIBUTION</h3>
      <p>Our secure facility can accommod.</p>
      <svg class="chev" width="20" height="16" viewBox="0 0 20 16"><path d="M3 2l7 6 7-6M3 8l7 6 7-6" stroke="#0355a3" stroke-width="2" fill="none"/></svg>
    </article>
    <article class="card">
      <div class="photo" role="img" aria-label="Red semi truck on an open road" style="background:linear-gradient(180deg,#8fb7de,#c9b28a 60%,#7a4a3a)"></div>
      <div class="icon"><svg width="30" height="24" viewBox="0 0 30 24"><circle cx="9" cy="7" r="4" fill="#fff"/><circle cx="21" cy="7" r="4" fill="#fff"/><path d="M2 22c0-6 3-9 7-9s7 3 7 9zM14 22c0-6 3-9 7-9s7 3 7 9z" fill="#fff"/></svg></div>
      <h3>CARRIERS</h3>
      <p>Are you a carrier looking to work with Brightlane? Click here to find.</p>
      <svg class="chev" width="20" height="16" viewBox="0 0 20 16"><path d="M3 2l7 6 7-6M3 8l7 6 7-6" stroke="#0355a3" stroke-width="2" fill="none"/></svg>
    </article>
  </div>
</section>

<section class="updates">
  <div class="photo" role="img" aria-label="Loaded container ship sailing on open water"></div>
  <div class="panel">
    <h2 class="title">GET UPDATES</h2>
    <p>We occasionally send out news and related industry articles. Sign up and we promise to deliver quality information to you.</p>
    <div class="form">
      <div class="field">First Name*</div>
      <div class="field">Last Name*</div>
      <div class="field">Organization*</div>
      <div class="field">Email*</div>
      <div class="btn-outline">SUBMIT</div>
    </div>
  </div>
</section>

<section class="about">
  <h2 class="title">BRIGHTLANE TRANSPORTATION</h2>
  <p class="subtitle">Vision And Mission</p>
  <div class="tabs">
    <div class="tab is-active" style="width:176px">FOUNDER</div>
    <div class="tab" style="width:154px">VISION</div>
    <div class="tab" style="width:158px">MISSION</div>
  </div>
  <div class="tab-panel">
    <div class="founder-photo" role="img" aria-label="Portrait of the company founder"></div>
    <div class="founder-text">
      <h4>FOUNDER</h4>
      <p>Brightlane Transportation welcomes you to our growing family of clients! We have over 26 years of experience in helping people solve their logistics needs from coast-to-coast.</p>
      <p>We also provide friendly, exceptional service that makes it easy to do business with us.</p>
      <p class="sign">Relax, we got this!</p>
    </div>
  </div>
  <div class="photo" role="img" aria-label="Rows of stacked shipping containers at a terminal"></div>
  <div class="live-chat"><span>&#9679; LIVE CHAT</span></div>
</section>

<section class="reviews" role="img" aria-label="Blue tinted highway and truck background">
  <h2 class="title">WHAT OUR CLIENT SAY</h2>
  <p class="subtitle">Best Reviews</p>
  <div class="avatar" role="img" aria-label="Client portrait"></div>
  <blockquote>"Lorem Ipsum is simply dummy text of the printing and typesetting industry. Lorem Ipsum has been the industry's standard dummy text ever since the 1500s, when an unknown printer took a galley of type."</blockquote>
  <cite>– <b>CLIENT NAME</b> (company.com)</cite>
  <svg class="rev-arrow" style="left:80px" width="16" height="30" viewBox="0 0 16 30"><path d="M14 2 2 15l12 13" stroke="#fff" stroke-width="2" fill="none"/></svg>
  <svg class="rev-arrow" style="right:80px" width="16" height="30" viewBox="0 0 16 30"><path d="m2 2 12 13L2 28" stroke="#fff" stroke-width="2" fill="none"/></svg>
</section>

<section class="contact">
  <h2 class="title">GET IN TOUCH WITH US</h2>
  <p class="subtitle">CONTACT US</p>
  <div class="map" style="left:78px" role="img" aria-label="Street map of the downtown office"></div>
  <div class="map" style="left:426px" role="img" aria-label="Street map of the suburban office"></div>
  <div class="info">
    <div class="brand" style="position:static">
      <span class="brand-name">Brightlane</span>
      <span class="brand-sub">Transportation,<br>Distribution &amp;<br>Warehousing Inc.</span>
    </div>
    <ul>
      <li><svg width="18" height="22" viewBox="0 0 18 22"><path d="M9 1C4.5 1 1 4.5 1 9c0 6 8 12 8 12s8-6 8-12c0-4.5-3.5-8-8-8z" fill="#0355a3"/><circle cx="9" cy="9" r="3" fill="#fff"/></svg><span><b>BRIGHTLANE</b><br>418 Maple Row Suite 210<br>Kestrel Park, ST 00417</span></li>
      <li><svg width="18" height="18" viewBox="0 0 18 18"><path d="M4 1l3 4-2 2c1 2 3 4 5 5l2-2 4 3-2 3C8 16 2 10 1 4z" fill="#0355a3"/></svg><span>Office: 555.014.5200<br>Warehouse: 555.014.9202</span></li>
      <li><svg width="18" height="18" viewBox="0 0 18 18"><rect x="2" y="6" width="14" height="9" fill="#0355a3"/><rect x="5" y="2" width="8" height="5" fill="none" stroke="#0355a3" stroke-width="1.5"/></svg><span>555.014.9201</span></li>
      <li><svg width="18" height="14" viewBox="0 0 18 14"><rect x="1" y="1" width="16" height="12" fill="none" stroke="#0355a3" stroke-width="1.5"/><path d="m1 1 8 7 8-7" stroke="#0355a3" stroke-width="1.5" fill="none"/></svg><span>info@brightlanefreight.com</span></li>
    </ul>
    <div class="socials">
      <i style="background:var(--blue)"></i>
      <i style="background:var(--sky)"></i>
      <i style="border:2px solid #c5c9ce"></i>
    </div>
  </div>
</section>

<section class="partners">
  <div class="round-arrow" style="left:134px"><svg width="10" height="16" viewBox="0 0 10 16"><path d="M8 2 2 8l6 6" stroke="#0355a3" stroke-width="2" fill="none"/></svg></div>
  <div class="round-arrow" style="left:1022px"><svg width="10" height="16" viewBox="0 0 10 16"><path d="m2 2 6 6-6 6" stroke="#0355a3" stroke-width="2" fill="none"/></svg></div>
  <div class="badge" style="left:262px;top:52px;width:160px;height:72px;border-radius:4px"></div>
  <div class="badge" style="left:476px;top:48px;width:126px;height:80px;border-radius:6px"></div>
  <div class="badge" style="left:654px;top:46px;width:84px;height:84px;border-radius:50%"></div>
  <div class="badge" style="left:792px;top:54px;width:168px;height:68px;border-radius:4px"></div>
</section>

<footer class="site-footer">
  <div class="col" style="left:78px;width:240px;top:44px">
    <div style="display:flex;align-items:center;gap:10px">
      <span class="brand-name" style="color:#fff;font-size:34px">Brightlane</span>
      <span class="brand-sub" style="color:#fff;font-size:10px;line-height:12px">Transportation,<br>Distribution &amp;<br>Warehousing Inc.</span>
    </div>
    <p style="margin-top:22px">Brightlane Transportation welcomes you to our growing family of clients! We have over 26 years of experience in helping people solve their logistics needs from coast-to-coast.</p>
    <p style="margin-top:12px">We also provide friendly, exceptional service that makes it easy to do business with us.</p>
  </div>
  <div class="col" style="left:355px">
    <h5>USEFULL LINKS</h5>
    <ul style="margin-top:16px">
      <li>What We Do</li><li>How We Do It</li><li>Who We Are</li><li>Tracking</li><li>Chat</li><li>Contact</li>
    </ul>
  </div>
  <div class="col" style="left:609px">
    <h5>WHAT WE DO</h5>
    <ul style="margin-top:16px">
      <li>Freight Management</li><li>Truckload</li><li>Less-Than-Truckload (LTL)</li><li>Volume LTL Expedited</li><li>Rail Shipments</li><li>International</li><li>Inbound Logistics</li><li>Freight Bill Auditing</li><li>Warehousing &amp; Distribution</li><li>Kitting</li><li>Fulfillment</li>
    </ul>
  </div>
  <div class="col" style="left:874px;width:250px">
    <h5>NEWSLETTER</h5>
    <p style="margin-top:14px;font-size:13px;line-height:21px">Would you like to receive exclusive access to articles, white papers and our regular monthly newsletter?</p>
    <div class="subscribe-input">Enter Email Id</div>
    <div class="subscribe-btn">SUBSCRIBE</div>
  </div>
</footer>
<div class="bottom-bar">© BRIGHTLANE - 2017. All Rights Reserved</div>

</body>
</html>
```